wardrobe/costume stylist needs good business card for own business

Hi:)

I'm wanting a business card for my company. I am a freelance stylist.

I do wardrobe/costume stylist to TV commercials; Films; Fashion and Lifestyle shoots.

I'd like a design based around my name Rosalind Parfrey written nicely, maybe a colour? Up to you?!

I've attached a couple of images of business cards I like
.... be creative and have fun!

Thank you :)

Reason: I was trying to get my new business card ready for before I headed overseas Friday morning but I don't think that was realistic so I'd like to extend the deadline to give time to the project. Thank you

Hi designers:) Thank you for all your designs, I've extended the deadline until Sunday, so there's a bit more time. I've attached 3 pictures of business cards which I quite like, please take a look to see if it can be of help in your process. I like the pale plain or patterned background with dark font and the dark plain or patterned background with the pale font the motifs the feminine fonts the plain fonts I like the idea of playing with a circle or some shape on one side of the card with my name or initials as in the picture I have on my post could you play around with this idea a bit please? Thank you all for the work you've done :) Rosa

Hi I am working overseas til Saturday night sorry for no feedback until I teturn Thanks :) Rosa

Hi designers, Thank you all so much for submitting your designs, I really appreciate your input into my project :) I'm sorry I didn't get to respond to some comments, and give feedback. I didn't back from being away until later than I expected, and the deadline had passed then, so apologies. Thanks to you all again for all your really good designs :) Rosa

Target Market(s)

I am a freelance stylist my target audience is producers, production companies, photographers, directors...

Industry/Entity Type

Business

Requirements
Must have
• Rosalind Parfrey
Stylist or Wardrobe Stylist

email rosaparfrey@mailbox-example.co.nz
Mobile 0218467193

(Don't have to use the words 'email' and 'mobile')
Nice to have
• Would like it to be double sided
Like B & W
Like pale colour background with dark font or white font
Like dark colour background with pale font
Should not have
• I would prefer it not to incorporate pictures

```html
<!DOCTYPE html>
<html lang="en">
<head>
<meta charset="utf-8">
<title>Rosalind Parfrey – Wardrobe Stylist</title>
<link rel="stylesheet" href="https://fonts.googleapis.com/css2?family=Germania+One&family=Josefin+Sans:wght@300;400&display=swap">
<style>
  :root {
    --card-black: #000000;
    --ink-white: #ffffff;
    --rule-grey: #8a8a8a;
    --flourish-red: #a81e22;
    --flourish-deep: #5e1012;
  }
  html, body {
    margin: 0;
    padding: 0;
    width: 1200px;
    height: 702px;
    overflow: hidden;
    background: var(--card-black);
  }
  .card {
    position: relative;
    width: 1200px;
    height: 702px;
    background: var(--card-black);
    overflow: hidden;
  }
  .flourish {
    position: absolute;
    left: -120px;
    top: -20px;
    width: 600px;
    height: 540px;
  }
  .identity__name {
    position: absolute;
    left: 500px;
    top: 299px;
    width: 600px;
    margin: 0;
    text-align: center;
    font-family: "Germania One", serif;
    font-weight: 400;
    font-size: 86px;
    line-height: 1;
    color: var(--ink-white);
    white-space: nowrap;
    transform: scaleY(1.7);
    transform-origin: 50% 69px;
  }
  .identity__rule {
    position: absolute;
    left: 531px;
    top: 410px;
    width: 542px;
    height: 1px;
    margin: 0;
    border: 0;
    background: var(--rule-grey);
  }
  .identity__role {
    position: absolute;
    left: 500px;
    top: 428px;
    width: 600px;
    margin: 0;
    text-align: center;
    font-family: "Josefin Sans", sans-serif;
    font-weight: 300;
    font-size: 40px;
    line-height: 1;
    letter-spacing: 11px;
    text-indent: 11px;
    color: var(--ink-white);
    white-space: nowrap;
    transform: scaleY(1.35);
    transform-origin: 50% 0;
  }
</style>
</head>
<body>
  <main class="card">
    <svg class="flourish" viewBox="0 0 600 540" role="img" aria-label="Decorative red swirling floral flourish in the top-left corner">
      <defs>
        <radialGradient id="flourish-glow" cx="0.5" cy="0.5" r="0.5">
          <stop offset="0" stop-color="var(--flourish-red)" stop-opacity="1"/>
          <stop offset="0.5" stop-color="var(--flourish-deep)" stop-opacity="0.8"/>
          <stop offset="1" stop-color="var(--card-black)" stop-opacity="0"/>
        </radialGradient>
      </defs>
      <rect width="600" height="540" fill="url(#flourish-glow)"/>
    </svg>

    <h1 class="identity__name">Rosalind Parfrey</h1>
    <hr class="identity__rule">
    <p class="identity__role">WARDROBE STYLIST</p>
  </main>
</body>
</html>
```